Need Business Card ASAP

We need a business card design for a meeting coming up in a few days. The company name is Harlow Ridge Building and Construction and the logo is attached. Something clean, cool, and contemporary that we can get to a printer right away. Attached is the business card for Volmar Energy, an affiliated company, which we like. Instead of the hawk on the back, you could use the attached "D". We'll also be needing matching letterhead in the near future, so ideas for that are welcome.

```html
<!DOCTYPE html>
<html lang="en">
<head>
<meta charset="utf-8">
<title>Harlow Ridge Building and Construction – Business Card</title>
<link href="https://fonts.googleapis.com/css2?family=Source+Sans+3:wght@400;600;700&display=swap" rel="stylesheet">
<style>
  :root {
    --backdrop: #e9e4da;
    --card-white: #ffffff;
    --olive: #c8c496;
    --olive-deep: #b3ad78;
    --olive-text: #b5ad72;
    --ink: #1f1f1f;
    --text-grey: #3a3a3a;
    --rule: #d6d6d6;
  }
  * { box-sizing: border-box; margin: 0; padding: 0; }
  html, body {
    width: 1016px; height: 1200px; overflow: hidden;
    background: var(--backdrop);
    font-family: "Source Sans 3", "Helvetica Neue", Arial, sans-serif;
  }
  .canvas { position: relative; width: 1016px; height: 1200px; }

  /* Front of card */
  .card-front {
    position: absolute; left: 71px; top: 63px; width: 872px; height: 498px;
    background: var(--card-white);
    box-shadow: 0 4px 14px rgba(0,0,0,.18);
  }
  .edge-band { position: absolute; top: 0; width: 16px; height: 100%; }
  .edge-band--left { left: 0; }
  .edge-band--right { right: 0; }
  .edge-band__top { height: 232px; background: var(--olive); }
  .edge-band__bottom { height: 266px; background: var(--ink); }

  .brand-block {
    position: absolute; left: 158px; top: 88px; width: 179px; height: 231px;
    display: flex; flex-direction: column; justify-content: center; align-items: flex-start;
    gap: 14px; padding: 0 12px;
  }
  .brand-block__square { width: 34px; height: 34px; background: var(--olive); }
  .brand-block__name {
    font-weight: 700; font-size: 22px; line-height: 1.15; color: var(--ink);
  }

  .divider-vertical {
    position: absolute; left: 370px; top: 88px; width: 2px; height: 233px;
    background: linear-gradient(to bottom, rgba(200,200,200,0), #bdbdbd 50%, rgba(200,200,200,0));
  }

  .contact { position: absolute; left: 397px; top: 80px; }
  .contact__name { font-weight: 700; font-size: 33px; color: var(--olive-text); line-height: 1.1; }
  .contact__title { font-weight: 600; font-size: 23px; color: var(--text-grey); margin-top: 6px; }
  .contact__list { list-style: none; margin-top: 22px; }
  .contact__item {
    display: flex; align-items: center; gap: 10px;
    font-size: 25px; color: var(--text-grey); height: 41px;
  }
  .contact__icon { width: 20px; height: 20px; flex: none; }

  .divider-horizontal {
    position: absolute; left: 120px; right: 120px; top: 384px; height: 2px;
    background: linear-gradient(to right, rgba(210,210,210,0), var(--rule) 50%, rgba(210,210,210,0));
  }
  .company-line {
    position: absolute; left: 0; width: 100%; top: 405px; text-align: center;
  }
  .company-line__name { font-weight: 600; font-size: 30px; color: var(--olive-text); }
  .company-line__address { font-size: 22px; color: var(--ink); margin-top: 2px; }

  /* Back of card */
  .card-back {
    position: absolute; left: 66px; top: 594px; width: 872px; height: 530px;
    background: var(--olive);
    box-shadow: 0 4px 14px rgba(0,0,0,.18);
  }
  .card-back__brand {
    position: absolute; left: 40px; top: 190px; width: 370px;
    font-weight: 700; font-size: 38px; line-height: 1.15; color: var(--card-white);
  }
  .card-back__url {
    position: absolute; left: 448px; top: 244px;
    font-weight: 700; font-size: 25px; color: var(--text-grey);
  }
</style>
</head>
<body>
<div class="canvas">

  <section class="card-front" aria-label="Business card front">
    <div class="edge-band edge-band--left"><div class="edge-band__top"></div><div class="edge-band__bottom"></div></div>
    <div class="edge-band edge-band--right"><div class="edge-band__top"></div><div class="edge-band__bottom"></div></div>

    <div class="brand-block">
      <div class="brand-block__square"></div>
      <div class="brand-block__name">Harlow Ridge Building and Construction</div>
    </div>

    <div class="divider-vertical"></div>

    <div class="contact">
      <div class="contact__name">Your Name</div>
      <div class="contact__title">Title</div>
      <ul class="contact__list">
        <li class="contact__item">
          <svg class="contact__icon" viewBox="0 0 20 20"><path d="M5 2 L8 2 L9 6 L7 8 Q9 12 12 13 L14 11 L18 12 L18 15 Q17 18 14 18 Q4 16 2 5 Q2 2 5 2 Z" fill="none" stroke="#3a3a3a" stroke-width="1.6"/></svg>
          (123) 456-7890
        </li>
        <li class="contact__item">
          <svg class="contact__icon" viewBox="0 0 20 20"><rect x="6" y="1.5" width="8" height="17" rx="1.5" fill="none" stroke="#3a3a3a" stroke-width="1.6"/><rect x="7.8" y="4" width="4.4" height="6" fill="#3a3a3a"/></svg>
          (123) 456-7890
        </li>
        <li class="contact__item">
          <svg class="contact__icon" viewBox="0 0 20 20"><rect x="2" y="5" width="16" height="11" fill="#3a3a3a"/><path d="M2 5 L10 11 L18 5" fill="none" stroke="#fff" stroke-width="1.4"/></svg>
          yourname@harlowridge.com
        </li>
        <li class="contact__item">
          <svg class="contact__icon" viewBox="0 0 20 20"><circle cx="10" cy="10" r="8" fill="none" stroke="#3a3a3a" stroke-width="1.5"/><ellipse cx="10" cy="10" rx="3.5" ry="8" fill="none" stroke="#3a3a3a" stroke-width="1.2"/><line x1="2" y1="10" x2="18" y2="10" stroke="#3a3a3a" stroke-width="1.2"/></svg>
          www.harlowridge.com
        </li>
      </ul>
    </div>

    <div class="divider-horizontal"></div>

    <div class="company-line">
      <div class="company-line__name">Harlow Ridge Building &amp; Construction</div>
      <div class="company-line__address">00, Complex Name, Street, City 00000</div>
    </div>
  </section>

  <section class="card-back" aria-label="Business card back">
    <div class="card-back__brand">Harlow Ridge Building and Construction</div>
    <div class="card-back__url">www.harlowridgebuilding.com</div>
  </section>

</div>
</body>
</html>
```